Redesign Website - Current one too plain

The description is in the uploaded file. Please let me know if you need any more information. I'd prefer it if someone could implement the design to a WordPress site but the best design will win, regardless.
I would like the forms to look nice as well
UPDATE:
I don't think we can use the images that I provided, I think they make the site look a bit 'cheap' and I really don't know how to replace them. One thought I have had is to make the "Simple, Unique, Effective" a second feature on the right side of the page with the search on the left
Target Market(s)
Small companies, private sellers of cars and people who rent their caravan/holiday home out
Industry/Entity Type
Advertising
Number of Pages Required
3 page
Colors
Designer to choose colors to be used in the design.
Look and feel
Each slider illustrates characteristics of the customer's brand and the style your logo design should communicate.

```html
<!DOCTYPE html>
<html lang="en">
<head>
<meta charset="utf-8">
<title>KARNO – Advertise with a simple code</title>
<link href="https://fonts.googleapis.com/css2?family=Poppins:wght@400;500;600;700&family=Arimo:wght@700&display=swap" rel="stylesheet">
<style>
:root{
  --blue:#0046a8;
  --blue-dark:#003d95;
  --yellow:#f8fb00;
  --ink:#2b2b2b;
  --muted:#5d5d5d;
  --hero-bg:#e6e6e6;
  --footer:#2a2a2a;
  --white:#ffffff;
}
*{margin:0;padding:0;box-sizing:border-box}
html,body{width:1200px;height:2753px;overflow:hidden}
body{font-family:"Poppins",sans-serif;color:var(--ink);background:var(--white);position:relative}
.abs{position:absolute}
.heading{font-family:"Arimo",sans-serif;font-weight:700;letter-spacing:.5px}
.btn{position:absolute;display:flex;align-items:center;justify-content:center;font-weight:600;font-size:13px;letter-spacing:.3px;border-radius:4px}
.btn-yellow{background:var(--yellow);color:var(--ink);box-shadow:0 6px 14px rgba(0,0,0,.12)}
.btn-blue{background:var(--blue);color:var(--white)}
.logo{position:absolute;display:flex;align-items:center;gap:18px}
.logo-mark{width:34px;height:34px;border-radius:50%;background:var(--yellow)}
.logo-name{font-family:"Poppins",sans-serif;font-weight:600;font-size:46px;letter-spacing:14px;color:var(--yellow);line-height:1}

/* header */
.site-header{position:absolute;left:0;top:0;width:1200px;height:120px;background:var(--white)}
.main-nav{position:absolute;top:50px;left:535px;display:flex;gap:34px;font-size:14px;font-weight:600}
.main-nav .active{color:var(--blue)}

/* hero */
.hero{position:absolute;left:0;top:120px;width:1200px;height:518px;background:linear-gradient(135deg,#ececec,#dedede 50%,#e9e9e9)}
.hero-title{left:111px;top:132px;font-size:46px;color:#333}
.hero-lead{left:111px;top:196px;width:360px;font-size:19px;line-height:29px;color:#444}
.tab{position:absolute;top:274px;width:110px;height:46px;background:var(--white);border-radius:4px;display:flex;align-items:center;justify-content:center;font-size:13px;font-weight:600;color:var(--blue)}
.search-box{position:absolute;left:111px;top:332px;width:229px;height:46px;background:var(--white);border-radius:4px;display:flex;align-items:center;font-size:13px;font-weight:600;color:var(--blue)}
.search-box .field{flex:1;display:flex;justify-content:space-between;align-items:center;padding:0 12px 0 18px}
.search-box .sep{width:1px;height:22px;background:#ddd}
.hero-visual{left:510px;top:110px;width:670px;height:300px;border-radius:40px;background:radial-gradient(ellipse at 50% 60%,#9a9a9a,#bdbdbd 50%,rgba(220,220,220,0) 72%)}

/* sections */
.section-title{position:absolute;left:0;width:1200px;text-align:center;font-size:38px;color:var(--blue)}
.underline{position:absolute;width:76px;height:3px;background:var(--yellow)}
.about-text{position:absolute;left:111px;top:822px;width:978px;text-align:center;font-size:16.5px;line-height:28.5px;color:#333}

.features{position:absolute;left:0;top:1105px;width:1200px;height:566px;background:var(--yellow)}
.card{position:absolute;top:174px;width:297px;height:308px;background:var(--white);border-bottom:4px solid var(--blue);box-shadow:0 4px 14px rgba(0,0,0,.08);text-align:center}
.card-icon{width:90px;height:90px;border-radius:50%;background:var(--yellow);margin:40px auto 0;display:flex;align-items:center;justify-content:center}
.card h3{font-size:18px;font-weight:600;color:var(--blue);margin-top:28px;letter-spacing:.3px}
.card p{font-size:16px;line-height:27.5px;color:var(--muted);margin:9px 30px 0}

.advertise{position:absolute;left:0;top:1671px;width:1200px;height:266px;background:linear-gradient(120deg,var(--blue),var(--blue-dark))}
.advertise h2{position:absolute;left:111px;top:68px;font-size:36px;color:var(--white)}
.advertise p{position:absolute;left:110px;top:137px;width:680px;font-size:16.5px;line-height:28.5px;color:var(--white);font-weight:500}

.review{position:absolute;top:2136px;width:305px;height:276px;background:var(--white);box-shadow:0 4px 16px rgba(0,0,0,.09);padding:22px 23px}
.stars{color:#e4a10f;font-size:15px;letter-spacing:2px}
.review p{font-size:15px;line-height:24.5px;color:#666;text-align:justify;margin-top:6px;padding-bottom:14px;border-bottom:1px solid #ddd}
.author{display:flex;align-items:center;gap:19px;margin-top:20px}
.avatar{width:56px;height:56px;border-radius:50%;background:linear-gradient(#c9b7a4,#8f8378)}
.author strong{display:block;font-size:13.5px;color:var(--blue);font-weight:600}
.author span{font-size:11.5px;color:#444}
.arrow{position:absolute;width:36px;height:36px;border-radius:50%;display:flex;align-items:center;justify-content:center}

.site-footer{position:absolute;left:0;top:2527px;width:1200px;height:226px;background:var(--footer)}
.footer-nav{position:absolute;left:565px;top:88px;display:flex;gap:26px;font-size:14.5px;font-weight:600;color:var(--white)}
.footer-rule{position:absolute;left:111px;top:151px;width:978px;height:1px;background:#555}
.copyright{position:absolute;left:0;top:176px;width:1200px;text-align:center;font-size:14px;color:var(--white)}
</style>
</head>
<body>

<header class="site-header">
  <div class="logo" style="left:111px;top:38px"><span class="logo-mark"></span><span class="logo-name">KARNO</span></div>
  <nav class="main-nav"><span class="active">HOME</span><span>ADVERTISE</span><span>CONTACT</span></nav>
  <a class="btn btn-blue" style="left:847px;top:37px;width:116px;height:46px">
    <svg width="11" height="12" viewBox="0 0 11 12" style="margin-right:8px"><circle cx="5.5" cy="3" r="3" fill="#fff"/><path d="M0 12c0-4 2.5-5.5 5.5-5.5S11 8 11 12z" fill="#fff"/></svg>LOGIN</a>
  <a class="btn btn-yellow" style="left:972px;top:37px;width:117px;height:46px;box-shadow:none">REGISTER</a>
</header>

<section class="hero">
  <h1 class="abs heading hero-title">KARNO</h1>
  <p class="abs hero-lead">Lorem ipsum dolor sit amet, conse ctetur adipiscing elit.</p>
  <span class="tab" style="left:111px">CAR</span>
  <span class="tab" style="left:231px">CARAVAN</span>
  <span class="tab" style="left:351px">COMPANY</span>
  <div class="search-box">
    <div class="field">A <svg width="10" height="6"><path d="M1 1l4 4 4-4" stroke="#888" fill="none"/></svg></div>
    <span class="sep"></span>
    <div class="field">1 <svg width="10" height="6"><path d="M1 1l4 4 4-4" stroke="#888" fill="none"/></svg></div>
  </div>
  <a class="btn btn-yellow" style="left:351px;top:332px;width:110px;height:46px;box-shadow:none">SEARCH</a>
  <div class="abs hero-visual" role="img" aria-label="Silver van, grey SUV and static caravan with short code plates"></div>
</section>

<section>
  <h2 class="section-title heading" style="top:745px">ABOUT KARNO</h2>
  <span class="underline" style="left:562px;top:791px"></span>
  <p class="about-text">Lorem ipsum dolor sit amet, consectetur adipiscing elit, sed do eiusmod tempor incididunt ut labore et dolore magna aliqua. Ut enim ad minim veniam, quis nostrud exercitation ullamco laboris nisi ut aliquip ex ea commodo consequat. Duis aute irure dolor in reprehenderit in voluptate velit esse cillum dolore eu fugiat nulla pariatur. Excepteur sint occaecat cupidatat non qui officia deserunt mollit anim id est laborum.</p>
  <a class="btn btn-yellow" style="left:532px;top:963px;width:136px;height:45px">CONTACT US</a>
</section>

<section class="features">
  <h2 class="section-title heading" style="top:75px">SIMPLE. UNIQUE. EFFECTIVE.</h2>
  <span class="underline" style="left:562px;top:122px;background:var(--blue)"></span>
  <div class="card" style="left:111px">
    <div class="card-icon" role="img" aria-label="Gear with pointing hand icon"></div>
    <h3>SIMPLE</h3><p>Create your advert and display your code</p>
  </div>
  <div class="card" style="left:452px">
    <div class="card-icon" role="img" aria-label="Gear with star icon"></div>
    <h3>UNIQUE</h3><p>Customers find you by an easy-to-remember code</p>
  </div>
  <div class="card" style="left:792px">
    <div class="card-icon" role="img" aria-label="Hand holding gears icon"></div>
    <h3>EFFECTIVE</h3><p>Customers are directed to you and not a list of your competitors.</p>
  </div>
</section>

<section class="advertise">
  <h2 class="heading">ADVERTISE YOUR COMPANY</h2>
  <span class="underline" style="left:111px;top:114px"></span>
  <p>Lorem ipsum dolor sit amet, consectetur adipiscing elit, sed do eiusmod tempor incididunt ut labore et dolore magna.</p>
  <a class="btn btn-yellow" style="left:936px;top:109px;width:153px;height:47px;box-shadow:none">ADVERTISE NOW</a>
</section>

<section>
  <h2 class="section-title heading" style="top:2041px">TESTIMONIALS</h2>
  <span class="underline" style="left:562px;top:2087px"></span>
  <span class="arrow" style="left:33px;top:2256px"><svg width="10" height="16"><path d="M8 2L2 8l6 6" stroke="#0046a8" stroke-width="2" fill="none"/></svg></span>
  <article class="review" style="left:111px"><div class="stars">★★★★★</div><p>Lorem ipsum dolor sit amet, consec tetur adipiscing elit, sed do eiusmod tempor incididunt ut labore et dolore magna aliqua.</p><div class="author"><span class="avatar" role="img" aria-label="Customer portrait"></span><div><strong>MARCUS HALE</strong><span>United States</span></div></div></article>
  <article class="review" style="left:447px"><div class="stars">★★★★★</div><p>Lorem ipsum dolor sit amet, consec tetur adipiscing elit, sed do eiusmod tempor incididunt ut labore et dolore magna aliqua.</p><div class="author"><span class="avatar" role="img" aria-label="Customer portrait"></span><div><strong>MARCUS HALE</strong><span>United States</span></div></div></article>
  <article class="review" style="left:783px"><div class="stars">★★★★★</div><p>Lorem ipsum dolor sit amet, consec tetur adipiscing elit, sed do eiusmod tempor incididunt ut labore et dolore magna aliqua.</p><div class="author"><span class="avatar" role="img" aria-label="Customer portrait"></span><div><strong>MARCUS HALE</strong><span>United States</span></div></div></article>
  <span class="arrow" style="left:1130px;top:2256px;background:var(--yellow)"><svg width="10" height="16"><path d="M2 2l6 6-6 6" stroke="#222" stroke-width="2" fill="none"/></svg></span>
</section>

<footer class="site-footer">
  <div class="logo" style="left:111px;top:68px"><span class="logo-mark"></span><span class="logo-name">KARNO</span></div>
  <nav class="footer-nav"><span>HOME</span><span>|</span><span>ADVERTISE</span><span>|</span><span>CONTACT</span><span>|</span><span>REGISTER</span><span>|</span><span>LOGIN</span></nav>
  <div class="footer-rule"></div>
  <p class="copyright">Copyrights © 2023 KARNO - All Rights Reserved.</p>
</footer>

</body>
</html>
```